KLV Plant Services

We are a heavy diesel mechanical business with additional air con certificates, remapping engine rebuilt

Contact Information for Business Card

Company Name, Director Name, Managing Director, Contact details, email and website

Font styles to use
Serif
Script

```html
<!DOCTYPE html>
<html lang="en">
<head>
<meta charset="utf-8">
<title>KLV Plant Services — Business Card</title>
<link href="https://fonts.googleapis.com/css2?family=Poppins:wght@400;500&family=Playfair+Display:wght@700&family=Great+Vibes&display=swap" rel="stylesheet">
<style>
  :root {
    --backdrop: #d4d4d0;
    --paper: #ffffff;
    --ink: #2b2b2b;
    --navy: #15157a;
    --edge: #1c1f8c;
    --charcoal: #343435;
    --charcoal-deep: #1f1f20;
    --muted: #4a4a4a;
    --serif: "Playfair Display", serif;
    --script: "Great Vibes", cursive;
    --sans: "Poppins", sans-serif;
  }
  * { box-sizing: border-box; margin: 0; padding: 0; }
  html, body { width: 1200px; height: 801px; overflow: hidden; }
  body {
    background: var(--backdrop);
    font-family: var(--sans);
    color: var(--ink);
    position: relative;
  }
  .card {
    position: absolute;
    top: 252px;
    width: 520px;
    height: 297px;
    border-bottom: 4px solid var(--edge);
    box-shadow: 0 14px 30px rgba(0,0,0,0.22);
  }
  .card--front { left: 50px; background: var(--paper); }
  .card--back { left: 630px; background: var(--charcoal); overflow: hidden; }

  .brand {
    position: absolute;
    top: 34px;
    right: 40px;
    display: flex;
    align-items: center;
    gap: 8px;
  }
  .brand__dot {
    width: 14px; height: 14px; border-radius: 50%;
    background: var(--navy);
  }
  .brand__name {
    font-family: var(--serif);
    font-weight: 700;
    font-size: 22px;
    line-height: 1;
    color: var(--navy);
  }

  .person { position: absolute; left: 40px; top: 124px; }
  .person__name {
    font-family: var(--serif);
    font-weight: 700;
    font-size: 21px;
    line-height: 1.1;
    color: var(--navy);
    text-transform: uppercase;
    letter-spacing: 0.5px;
  }
  .person__role {
    font-family: var(--script);
    font-size: 22px;
    line-height: 1.1;
    color: var(--muted);
    margin-top: 2px;
  }

  .address {
    position: absolute;
    right: 40px;
    top: 126px;
    text-align: right;
    font-style: normal;
    font-size: 12.5px;
    line-height: 1.5;
    color: var(--ink);
  }

  .contacts {
    position: absolute;
    left: 40px;
    bottom: 26px;
    list-style: none;
    font-size: 13px;
    line-height: 1.55;
  }
  .contacts li { display: flex; align-items: center; gap: 8px; }
  .contacts svg { width: 11px; height: 11px; flex: none; }
  .contacts .link { color: var(--navy); }

  .back__pattern {
    position: absolute; inset: 0;
    background:
      radial-gradient(ellipse at 75% 20%, rgba(255,255,255,0.07) 0%, rgba(255,255,255,0) 55%),
      linear-gradient(160deg, var(--charcoal) 0%, #2a2a2b 55%, var(--charcoal-deep) 100%);
  }
  .back__brand {
    position: absolute;
    right: 34px;
    bottom: 54px;
    display: flex;
    align-items: center;
    gap: 6px;
  }
  .back__brand .brand__dot { width: 9px; height: 9px; background: #ffffff; }
  .back__brand .brand__name { font-size: 13px; color: #ffffff; }
</style>
</head>
<body>

  <section class="card card--front">
    <div class="brand">
      <span class="brand__dot"></span>
      <span class="brand__name">KLV Plant Services</span>
    </div>

    <div class="person">
      <p class="person__name">Mark Ellison</p>
      <p class="person__role">Director</p>
    </div>

    <address class="address">
      2750 Harlow Rd Maple Grove<br>GA 30512
    </address>

    <ul class="contacts">
      <li>
        <svg viewBox="0 0 12 12" aria-hidden="true"><path d="M3 1 L5 3.5 L4 5 Q5.5 7 7 8 L8.5 7 L11 9 L9.5 11 Q5 10.5 1 3 Z" fill="var(--navy)"/></svg>
        470-555-0148
      </li>
      <li>
        <svg viewBox="0 0 12 12" aria-hidden="true"><rect x="1" y="2.5" width="10" height="7" fill="none" stroke="var(--navy)" stroke-width="1.3"/><path d="M1 2.5 L6 6.5 L11 2.5" fill="none" stroke="var(--navy)" stroke-width="1.3"/></svg>
        info@klvplantservices.com
      </li>
      <li>
        <svg viewBox="0 0 12 12" aria-hidden="true"><circle cx="6" cy="6" r="5" fill="var(--navy)"/><path d="M1 6 H11 M6 1 Q3 6 6 11 M6 1 Q9 6 6 11" fill="none" stroke="#fff" stroke-width="0.8"/></svg>
        <span>www.<span class="link">klvplantservices</span>.com</span>
      </li>
    </ul>
  </section>

  <section class="card card--back">
    <div class="back__pattern" role="img" aria-label="Repeating tone-on-tone brand pattern in dark gloss spot varnish across the charcoal card back"></div>
    <div class="back__brand">
      <span class="brand__dot"></span>
      <span class="brand__name">KLV Plant Services</span>
    </div>
  </section>

</body>
</html>
```